Exec Conference Design Concept

We need to refresh & update nonprofit association graphic design for annual meeting. The graphics will be used to promote the event primarily through digital communications & social media. Other materials we generate for this event are the agenda & billboard content. You can view the existing design at www.lutavorin.org under Events.

The target audience is primarily male, ages 35-60 in executive positions in C-Corps. The conference topics center on manufacturing regulations, marketing trends, and the economy. This conference has been around almost 30 years so we need something to invigorate potential registrants that will get their attention. It still needs to be professional and business-like.

In addition to a new design concept we would like to update the color palette. We’ve attached some mood boards with potential color & font suggestions. Our company logo is also attached and is the only design element tied to our branding that cannot be changed.

Designs should be energetic and sophisticated. Ideally, we would like the designs in Adobe Indesign or Photoshop. However, we can work with Illustrator.

Target Market(s)

Male business executives age 35-60.

Industry/Entity Type

Polystyrene manufacturing industry supply chain.

Other font styles liked:
• I usually prefer sans serif

Requirements
Must have
• Focus points to draw attention to higher level informational units. For example, some people will only read the headers and not detailed copy.
Nice to have
• Ways to insert bonus content that don’t over power other content. I like to see a good use of white space to enhance readability.

```html
<!DOCTYPE html>
<html lang="en">
<head>
<meta charset="UTF-8">
<title>Luta Expo 2026 – Navigating the Business of Tomorrow</title>
<link rel="stylesheet" href="https://fonts.googleapis.com/css2?family=Barlow+Condensed:wght@400;500;600;700&family=Montserrat:wght@400;500&display=swap">
<style>
  :root {
    --olive: #9cad45;
    --ink: #0d110f;
    --brown: #a05c12;
    --brown-logo: #5a2a12;
    --white: #ffffff;
    --stage: #ececec;
    --display-font: "Barlow Condensed", "Arial Narrow", sans-serif;
    --body-font: "Montserrat", Arial, sans-serif;
  }
  * { box-sizing: border-box; margin: 0; padding: 0; }
  html, body { width: 766px; height: 1200px; overflow: hidden; }
  body { background: var(--stage); position: relative; }

  .flyer {
    position: absolute; left: 63px; top: 19px;
    width: 640px; height: 1162px;
    background: var(--white); overflow: hidden;
  }
  .flyer > * { position: absolute; }

  .brand {
    left: 0; width: 640px; top: 80px;
    display: flex; justify-content: center; align-items: center; gap: 10px;
  }
  .brand-mark { width: 28px; height: 28px; background: var(--olive); border-radius: 4px; }
  .brand-name {
    font-family: var(--display-font); font-weight: 700; font-size: 48px; line-height: 1;
    color: var(--brown-logo);
  }

  .headline {
    left: 85px; top: 176px; width: 480px;
    font-family: var(--display-font); font-weight: 700; font-size: 51px; line-height: 46px;
    color: var(--ink); white-space: nowrap;
  }
  .edition-tag {
    left: 359px; top: 235px; width: 195px; height: 35px;
    border: 1.5px solid var(--olive);
    font-family: var(--display-font); font-weight: 400; font-size: 31px; line-height: 32px;
    color: var(--brown); text-align: center; white-space: nowrap;
  }
  .edition-tag strong { font-weight: 700; }
  .tagline {
    left: 85px; top: 289px; width: 480px;
    font-family: var(--display-font); font-weight: 600; font-size: 23.5px; line-height: 26px;
    color: var(--ink); white-space: nowrap;
  }

  .accent-band { left: 0; width: 640px; height: 9px; background: var(--olive); }
  .accent-band.top { top: 345px; }
  .accent-band.bottom { top: 1153px; }

  .hero-photo {
    left: 0; top: 354px; width: 640px; height: 295px;
    background: linear-gradient(100deg, #8a8f96 0%, #c9c6bd 35%, #e8e6e1 55%, #b9b8b2 75%, #3d73c4 100%);
  }

  .topics {
    left: 0; top: 649px; width: 640px; height: 251px;
    background: var(--ink);
  }
  .topic-icon { position: absolute; top: 14px; width: 44px; height: 44px; }
  .topic-title {
    position: absolute; top: 66px; width: 200px; text-align: center;
    font-family: var(--display-font); font-weight: 600; font-size: 27px; line-height: 22px;
    color: var(--olive);
  }
  .topic-points {
    position: absolute; top: 128px; list-style: none; padding-left: 9px;
    border-left: 1px solid rgba(156,173,69,0.6);
  }
  .topic-points li {
    position: relative; width: 140px;
    font-family: var(--body-font); font-size: 10.3px; line-height: 12.6px;
    color: var(--white); margin-bottom: 8px;
  }
  .topic-points li::before {
    content: ""; position: absolute; left: -12px; top: 3px;
    width: 5px; height: 5px; border-radius: 50%;
    border: 1px solid var(--olive); background: var(--ink);
  }

  .register-button {
    left: 180px; top: 874px; width: 280px; height: 52px;
    background: var(--brown); border-radius: 18px;
    font-family: var(--display-font); font-weight: 600; font-size: 34px; line-height: 52px;
    color: var(--white); text-align: center;
  }

  .bonus-card {
    left: 46px; top: 952px; width: 548px; height: 127px;
    border: 2px solid var(--ink);
  }
  .bonus-corner { position: absolute; right: -2px; top: -2px; width: 34px; height: 34px; }
  .bonus-thumb {
    position: absolute; left: 27px; top: 24px; width: 108px; height: 79px;
    background: linear-gradient(110deg, #141814 0%, #141814 65%, var(--olive) 72%, #6e7f9e 85%, #3d73c4 100%);
  }
  .bonus-title {
    position: absolute; left: 166px; top: 19px;
    font-family: var(--display-font); font-weight: 600; font-size: 27px; line-height: 28px;
    color: var(--ink); white-space: nowrap;
  }
  .bonus-text {
    position: absolute; left: 167px; top: 50px; width: 360px;
    font-family: var(--body-font); font-size: 10.6px; line-height: 13px; color: var(--ink);
  }
  .bonus-link {
    position: absolute; left: 167px; top: 82px;
    font-family: var(--body-font); font-weight: 500; font-size: 13.4px; line-height: 16px;
    color: var(--ink); text-decoration: underline; white-space: nowrap;
  }

  .site-footer {
    left: 0; top: 1096px; width: 640px; height: 57px; background: var(--ink);
  }
  .social-links { position: absolute; left: 46px; top: 18px; display: flex; gap: 5px; }
  .social-links span { width: 22px; height: 22px; border-radius: 50%; background: var(--white); }
  .contact-line {
    position: absolute; right: 46px; top: 17px;
    font-family: var(--display-font); font-weight: 400; font-size: 15px; line-height: 22px;
    color: var(--white); letter-spacing: 0.8px; white-space: nowrap;
  }
</style>
</head>
<body>
  <main class="flyer">
    <div class="brand">
      <span class="brand-mark"></span>
      <span class="brand-name">LUTA EXPO</span>
    </div>

    <h1 class="headline">NAVIGATING THE BUSINESS<br>OF TOMORROW</h1>
    <div class="edition-tag">LUTA EXPO <strong>2026</strong></div>
    <p class="tagline">DECADES OF LEADERSHIP, REIMAGINED FOR THE MODERN EXECUTIVE</p>

    <div class="accent-band top"></div>
    <div class="hero-photo" role="img" aria-label="Photo of a factory worker stacking white polystyrene boxes in a production hall with a forklift and blue machinery"></div>

    <section class="topics">
      <svg class="topic-icon" style="left:108px" viewBox="0 0 46 46" fill="none" stroke="#fff" stroke-width="1.6">
        <path d="M20 3h6l1 5 4 2 4-3 4 4-3 4 2 4 5 1v6l-5 1-2 4 3 4-4 4-4-3-4 2-1 5h-6l-1-5-4-2-4 3-4-4 3-4-2-4-5-1v-6l5-1 2-4-3-4 4-4 4 3 4-2z"/>
        <circle cx="23" cy="23" r="11"/>
        <circle cx="19" cy="19" r="2.5"/><circle cx="27" cy="27" r="2.5"/><circle cx="19" cy="27" r="2"/>
        <path d="M21 21l4 4M27 19l-2 2"/>
      </svg>
      <h2 class="topic-title" style="left:30px">MANUFACTURING<br>REGULATIONS</h2>
      <ul class="topic-points" style="left:56px">
        <li>Compliance in a changing world</li>
        <li>Policy impact on production</li>
      </ul>

      <svg class="topic-icon" style="left:311px" viewBox="0 0 46 46" fill="none" stroke="#fff" stroke-width="1.6">
        <path d="M4 18h8l16-10v30L12 28H4z"/>
        <path d="M8 28l3 12h5l-2-12"/>
        <path d="M28 16a7 7 0 0 1 0 14"/>
        <path d="M34 12l3-3M35 23h5M34 34l3 3"/>
      </svg>
      <h2 class="topic-title" style="left:233px">MARKETING<br>TRENDS</h2>
      <ul class="topic-points" style="left:268px">
        <li>Data-driven customer growth</li>
        <li>Digital transformation strategies</li>
      </ul>

      <svg class="topic-icon" style="left:503px" viewBox="0 0 46 46" fill="none" stroke="#fff" stroke-width="1.6">
        <path d="M4 40h38"/>
        <rect x="7" y="28" width="6" height="12"/><rect x="16" y="22" width="6" height="18"/>
        <rect x="25" y="25" width="6" height="15"/><rect x="34" y="14" width="6" height="26"/>
        <path d="M5 24l10-8 9 5 16-14M34 7h6v6"/>
      </svg>
      <h2 class="topic-title" style="left:425px">ECONOMIC<br>OUTLOOK</h2>
      <ul class="topic-points" style="left:467px">
        <li>Market risks and opportunities</li>
        <li>Forecasting industry growth</li>
      </ul>
    </section>

    <div class="register-button">REGISTER TODAY</div>

    <section class="bonus-card">
      <svg class="bonus-corner" viewBox="0 0 34 34"><path d="M0 0h34v34z" fill="#0d110f"/></svg>
      <div class="bonus-thumb" role="img" aria-label="Newsletter cover preview with a dark panel and a factory photo on the right"></div>
      <h3 class="bonus-title">BONUS CONTENT: EXECUTIVE INSIGHTS</h3>
      <p class="bonus-text">Exclusive insights from industry leaders to help you navigate change, adapt faster, and stay ahead.</p>
      <span class="bonus-link">Download Our Exclusive Monthly Newsletter</span>
    </section>

    <footer class="site-footer">
      <div class="social-links" aria-label="Social media links"><span></span><span></span><span></span></div>
      <p class="contact-line">(014) 276-5830 &nbsp;|&nbsp; www.lutavorin.org</p>
    </footer>
    <div class="accent-band bottom"></div>
  </main>
</body>
</html>
```